Design Brief for Website Redesign

Client Name: Harbourline IT
Website: www.harbourlineit.com.au
Industry: Managed IT Services
Target Audience: Small to medium-sized businesses in Australia, requiring IT solutions, IT support, cloud services, and phone systems.

Project Overview
We are seeking a full redesign of the Harbourline IT website to modernize its look, improve usability, and enhance user experience across devices. The goal is to create a professional, clean, and user-friendly website that reflects our expertise in IT services and appeals to our business clients.

Objectives
Modern Visual Identity: Create a fresh, modern design that aligns with Harbourline IT's branding.

Improved User Experience: Simplify navigation, improve accessibility, and enhance mobile responsiveness.

Clear Calls to Action: Ensure CTAs are prominent and encourage user engagement.

Enhanced Trust & Credibility: Highlight testimonials, case studies, and industry credentials.

SEO Optimization: Ensure the site is optimized for search engines, including proper heading structures and metadata.
Design Style & Tone
Professional: Clean, modern, and polished to reflect our IT expertise.

Minimalist: Simple layouts, plenty of white space, and easy-to-read typography.

Tech-focused: Subtle tech-themed design elements that reinforce our brand as a leading IT service provider.

Colors: Use our existing brand colors, or propose a color scheme that complements the tech industry while maintaining a professional feel.

Typography: Clear, readable fonts that convey professionalism and trustworthiness.

Key Pages & Features
Home Page:

Hero section with a clear value proposition.

Highlight key services (IT support, cloud solutions, phone systems, etc.) with icons and brief descriptions.

Prominent CTAs (e.g., “Request a Quote,” “Book a Demo”).

Testimonials from satisfied clients.

Services Page:

Detailed breakdown of the services we offer (IT support, cloud services, phone systems, etc.).

Use of icons or illustrations to make the services visually engaging.

Clear CTAs to request quotes or book consultations.

About Us Page:

Information about our company history, mission, and team.

Highlight our certifications, partnerships, and industry expertise.

Case Studies/Testimonials Page:

Showcase client success stories and testimonials with visuals and brief case study summaries.

Include a trust-building section with logos of major clients or partners.

Contact Page:

Simple contact form for inquiries.

Integrated map with office location.

Social media links and phone number.

Blog/Resource Section:

Easy-to-navigate blog section for IT-related articles, tips, and industry news.

Clear categorization and tags for easy browsing.

Knowledge Base/Support Page:

Self-service area for clients to find articles, FAQs, and support guides.

Option to submit a support ticket.

Mobile Responsiveness:

Ensure the design is fully responsive, with no horizontal scrolling or misaligned content on mobile.

Functional Requirements
Fast Load Times: Optimize images, minimize unnecessary scripts, and ensure the site loads quickly on both desktop and mobile.

User-Friendly CMS: We need a CMS that is easy to update (preferably WordPress, but open to other suggestions).

SEO Best Practices: Structure the site with proper metadata, alt tags, and semantic HTML for better search engine optimization.

Security: Ensure the website follows security best practices (SSL, HTTPS).

Deliverables
Full website design (desktop and mobile versions).

Design mockups in Photoshop, Sketch, or Figma (whichever is preferred).

Working prototype (optional).

Final website files, including images and assets.

A style guide for ongoing consistency.

Industry/Entity Type

IT Managed Services

Number of Pages Required

3 page

Requirements
Must have
• EXCELLENT UX/UI

```html
<!DOCTYPE html>
<html lang="en">
<head>
<meta charset="utf-8">
<title>Harbourline IT — Managed IT Services</title>
<meta name="description" content="Harbourline IT delivers IT support, cloud solutions, phone systems and cybersecurity for Australian businesses.">
<link href="https://fonts.googleapis.com/css2?family=Ubuntu:wght@400;500;700&display=swap" rel="stylesheet">
<style>
:root{
  --red:#e3173e;
  --red-dark:#c30f31;
  --ink:#111111;
  --navy:#07101f;
  --grey:#ececec;
  --text:#333;
  --white:#fff;
}
*{box-sizing:border-box;margin:0;padding:0}
html,body{width:1200px;height:2700px;overflow:hidden}
body{font-family:"Ubuntu",Arial,sans-serif;color:var(--text);background:var(--white);position:relative}
a{text-decoration:none;color:inherit}

/* header */
.site-header{position:absolute;top:0;left:0;width:1200px;height:72px;display:flex;align-items:center;justify-content:space-between;padding:0 90px 0 110px;background:var(--white)}
.brand{font-size:40px;font-weight:700;color:var(--red);letter-spacing:-1px}
.main-nav{display:flex;gap:14px;font-size:17px;color:var(--ink)}
.main-nav a{padding:8px 16px;border-radius:20px}
.main-nav a.active{background:var(--red);color:var(--white);box-shadow:0 0 0 2px #fff,0 0 0 3px var(--red)}

/* hero */
.hero{position:absolute;top:72px;left:0;width:1200px;height:570px;background:var(--navy);overflow:hidden}
.hero-visual{position:absolute;inset:0;background:
  radial-gradient(circle at 68% 48%,#4fb6ff 0,#1a5ea8 14%,#0c2c5a 32%,transparent 55%),
  linear-gradient(90deg,#05080f 0,#0a1a33 45%,#0c2447 70%,#08162c 100%)}
.hero-copy{position:absolute;left:124px;top:150px;width:430px;color:var(--white);border-left:6px solid var(--red);padding-left:14px}
.hero-copy h1{font-size:48px;font-weight:500;margin-bottom:14px}
.hero-copy p{font-size:15px;line-height:1.45;margin-bottom:20px}
.hero-actions{position:absolute;left:124px;top:352px;display:flex;gap:28px}
.btn{display:inline-block;font-size:16px;font-weight:500;padding:12px 26px;border-radius:26px}
.btn-red{background:var(--red);color:var(--white)}
.btn-outline{border:2px solid var(--white);color:var(--white)}
.btn-dark{background:var(--ink);color:var(--white)}

/* about */
.about{position:absolute;top:642px;left:0;width:1200px;height:520px;background:linear-gradient(180deg,var(--red) 0,var(--red-dark) 100%);text-align:center;color:var(--white)}
.about h2{font-size:42px;font-weight:500;margin-top:70px}
.about p{width:900px;margin:40px auto 32px;font-size:15px;line-height:1.6}
.about-curve{position:absolute;bottom:-1px;left:0}

/* services */
.section-title{font-size:44px;font-weight:500;color:var(--ink);text-align:center}
.section-title span{color:var(--red)}
.section-title::after{content:"";display:block;width:80px;height:3px;background:var(--red);margin:10px auto 0}
.services{position:absolute;top:1140px;left:0;width:1200px;height:600px}
.services .section-title{margin-top:10px}
.card-row{position:absolute;top:132px;left:120px;display:flex;gap:32px}
.service-card{position:relative;width:296px;height:400px;background:var(--white);border-radius:22px;box-shadow:0 8px 22px rgba(0,0,0,.16)}
.card-photo{height:208px;border-radius:22px;border-bottom:4px solid var(--red)}
.photo-support{background:linear-gradient(135deg,#c7d3df,#8397ad 60%,#3c4c62)}
.photo-cloud{background:linear-gradient(135deg,#1d3c68,#3c7fc0 50%,#0e1f3b)}
.photo-phone{background:linear-gradient(135deg,#d8cbbd,#9c8a7a 55%,#4b3d33)}
.card-icon{position:absolute;left:20px;top:180px;width:54px;height:54px;border-radius:50%;background:var(--white);border:3px solid var(--red);display:flex;align-items:center;justify-content:center}
.service-card h3{margin:40px 20px 8px;font-size:22px;font-weight:500;color:var(--ink)}
.service-card p{margin:0 20px;font-size:14px;line-height:1.45}
.service-card .btn{position:absolute;right:18px;bottom:18px;font-size:13px;padding:8px 16px}
.slider-arrow{position:absolute;top:340px;width:28px;height:28px;border-radius:50%;background:var(--ink);display:flex;align-items:center;justify-content:center}
.arrow-left{left:52px;background:#888}
.arrow-right{right:72px}

/* testimonials */
.testimonials{position:absolute;top:1740px;left:0;width:1200px;height:660px;background:var(--grey)}
.testimonials-curve{position:absolute;top:-60px;left:0}
.testimonials .section-title{margin-top:96px}
.testimonial-row{position:absolute;top:190px;left:144px;display:flex;gap:32px}
.testimonial-card{width:448px;height:312px;background:var(--white);border-radius:22px;padding:28px 28px;box-shadow:0 6px 16px rgba(0,0,0,.1)}
.t-head{display:flex;gap:18px;align-items:center}
.avatar{width:96px;height:96px;border-radius:50%;background:linear-gradient(160deg,#b9a690,#6c5a4a)}
.stars{display:flex;gap:4px;margin-bottom:4px}
.t-name{font-size:26px;font-weight:500;color:var(--ink)}
.t-role{font-size:12px;color:#777;margin-bottom:4px}
.t-client{font-size:14px;font-weight:700;color:var(--red)}
.t-company{font-size:24px;font-weight:500;color:var(--ink);margin:16px 0 10px}
.t-quote{font-size:14px;line-height:1.5}
.dots{position:absolute;top:560px;left:0;width:1200px;display:flex;justify-content:center;gap:8px}
.dots i{width:14px;height:14px;border-radius:50%;background:#c9c9c9}
.dots i.on{background:var(--red)}

/* footer */
.site-footer{position:absolute;top:2360px;left:0;width:1200px;height:340px;background:var(--ink);color:var(--white)}
.footer-curve{position:absolute;top:-60px;left:0}
.footer-brand{position:absolute;left:108px;top:112px;font-size:72px;line-height:1;font-weight:700;color:var(--red);letter-spacing:-1.5px;white-space:nowrap}
.footer-col{position:absolute;top:40px;border-left:4px solid var(--red);padding-left:18px}
.footer-col h4{font-size:26px;font-weight:500;margin-bottom:16px}
.footer-col li{list-style:none;font-size:15px;margin-bottom:10px;color:#ddd}
.footer-col li::before{content:"•";color:var(--red);margin-right:10px}
.col-quick{left:560px}
.col-useful{left:806px}
.footer-rule{position:absolute;left:108px;right:108px;top:268px;height:1px;background:#555}
.copyright{position:absolute;top:292px;width:1200px;text-align:center;font-size:13px;color:#ccc}
</style>
</head>
<body>

<header class="site-header">
  <a class="brand" href="#">harbourline</a>
  <nav class="main-nav">
    <a class="active" href="#">Home</a>
    <a href="#">Services</a>
    <a href="#">About Us</a>
    <a href="#">Testimonials</a>
    <a href="#">Resource</a>
    <a href="#">Contact</a>
  </nav>
</header>

<section class="hero">
  <div class="hero-visual" role="img" aria-label="Hand holding a glowing digital padlock surrounded by cybersecurity icons"></div>
  <div class="hero-copy">
    <h1>Cybersecurity</h1>
    <p>Ensure business continuity and prevent the risks of cyber attack with Harbourline IT's trusted cyber security solutions.</p>
    <p>Protect your business from data breaches</p>
  </div>
  <div class="hero-actions">
    <a class="btn btn-red" href="#">Request a Quote</a>
    <a class="btn btn-outline" href="#">Book a demo</a>
  </div>
</section>

<section class="about">
  <h2>About Harbourline IT</h2>
  <p>Founded in <strong>1997 in Sydney</strong>, Harbourline IT began as a dedicated IT managed services provider, delivering reliable technology solutions to local businesses. Since then, our expertise, services, and support have evolved significantly, transforming us into a leading End-to-End IT Solutions provider for Small &amp; Medium Businesses. Today, we proudly support offices across Australia, helping businesses streamline operations, enhance security, and embrace innovation.</p>
  <a class="btn btn-dark" href="#">Read More &#8250;</a>
  <svg class="about-curve" width="1200" height="90" viewBox="0 0 1200 90"><path d="M0 90 L0 60 Q600 -30 1200 60 L1200 90 Z" fill="#fff"/></svg>
</section>

<section class="services">
  <h2 class="section-title">Our <span>Services</span></h2>
  <div class="slider-arrow arrow-left"><svg width="12" height="12" viewBox="0 0 12 12"><path d="M8 1 L3 6 L8 11" stroke="#fff" stroke-width="2" fill="none"/></svg></div>
  <div class="card-row">
    <article class="service-card">
      <div class="card-photo photo-support" role="img" aria-label="Technician hands working with tools"></div>
      <div class="card-icon"><svg width="26" height="26" viewBox="0 0 24 24"><path d="M4 20 L13 11 M14 4 a5 5 0 0 0 6 6 l-3 -3z" stroke="#e3173e" stroke-width="2.2" fill="none" stroke-linecap="round"/></svg></div>
      <h3>IT support</h3>
      <p>Equipping your business to work optimally, with reliable and optimal managed services. Harbourline IT will</p>
      <a class="btn btn-dark" href="#">Know More &#8250;</a>
    </article>
    <article class="service-card">
      <div class="card-photo photo-cloud" role="img" aria-label="Engineer in a server room data centre"></div>
      <div class="card-icon"><svg width="28" height="28" viewBox="0 0 24 24"><path d="M7 18 h10 a4 4 0 0 0 0 -8 a5 5 0 0 0 -9.6 -1 A4.5 4.5 0 0 0 7 18z" stroke="#e3173e" stroke-width="2" fill="none"/></svg></div>
      <h3>Cloud Solutions</h3>
      <p>We offer a large spectrum of technology solutions, including cloud-based disaster recovery,</p>
      <a class="btn btn-red" href="#">Know More &#8250;</a>
    </article>
    <article class="service-card">
      <div class="card-photo photo-phone" role="img" aria-label="Hand using a smartphone"></div>
      <div class="card-icon"><svg width="24" height="24" viewBox="0 0 24 24"><path d="M5 3 h4 l2 5 -2.5 1.5 a11 11 0 0 0 6 6 L16 13 l5 2 v4 a2 2 0 0 1 -2 2 A16 16 0 0 1 3 5 a2 2 0 0 1 2 -2z" stroke="#e3173e" stroke-width="2" fill="none"/></svg></div>
      <h3>Phone Systems</h3>
      <p>Whether it's a basic landline paging or a major app project we can help you showcase your business in the best</p>
      <a class="btn btn-dark" href="#">Know More &#8250;</a>
    </article>
  </div>
  <div class="slider-arrow arrow-right"><svg width="12" height="12" viewBox="0 0 12 12"><path d="M4 1 L9 6 L4 11" stroke="#fff" stroke-width="2" fill="none"/></svg></div>
</section>

<section class="testimonials">
  <svg class="testimonials-curve" width="1200" height="61" viewBox="0 0 1200 61"><path d="M0 61 L0 40 Q600 -20 1200 40 L1200 61 Z" fill="#ececec"/></svg>
  <h2 class="section-title">Our <span>Testimonials</span></h2>
  <div class="testimonial-row">
    <article class="testimonial-card">
      <div class="t-head">
        <div class="avatar" role="img" aria-label="Portrait of client Daniel Whitford"></div>
        <div>
          <div class="stars">
            <svg width="100" height="18" viewBox="0 0 100 18"><g fill="#f2b01e"><path id="s" d="M9 1 l2.4 5 5.4 .6 -4 3.7 1.1 5.4 -4.9 -2.8 -4.9 2.8 1.1 -5.4 -4 -3.7 5.4 -.6z"/><use href="#s" x="20"/><use href="#s" x="40"/><use href="#s" x="60"/></g><use href="#s" x="80" fill="#ccc"/></svg>
          </div>
          <div class="t-name">Daniel Whitford</div>
          <div class="t-role">Managing Director</div>
          <div class="t-client">PARKWAY</div>
        </div>
      </div>
      <div class="t-company">Parkway Group</div>
      <p class="t-quote">Harbourline has been able to tailor their solutions to our changing needs. The engagement and ongoing services provided has meant we can get on with running our business, knowing that our technological foundation is in capable hands.</p>
    </article>
    <article class="testimonial-card">
      <div class="t-head">
        <div class="avatar" role="img" aria-label="Portrait of client Lena Marouf"></div>
        <div>
          <div class="stars">
            <svg width="100" height="18" viewBox="0 0 100 18"><g fill="#f2b01e"><path id="s2" d="M9 1 l2.4 5 5.4 .6 -4 3.7 1.1 5.4 -4.9 -2.8 -4.9 2.8 1.1 -5.4 -4 -3.7 5.4 -.6z"/><use href="#s2" x="20"/><use href="#s2" x="40"/><use href="#s2" x="60"/></g><use href="#s2" x="80" fill="#ccc"/></svg>
          </div>
          <div class="t-name">Lena Marouf</div>
          <div class="t-role">Principal/Senior Property Manager</div>
          <div class="t-client">COASTAL</div>
        </div>
      </div>
      <div class="t-company">Coastal Realty</div>
      <p class="t-quote">I wish to thank Harbourline IT for their outstanding services &amp; for looking after our business. The services they provide make the daily operation of our business very smooth. We would have not survived without them.</p>
    </article>
  </div>
  <div class="dots"><i class="on"></i><i></i><i></i><i></i></div>
</section>

<footer class="site-footer">
  <svg class="footer-curve" width="1200" height="61" viewBox="0 0 1200 61"><path d="M0 61 L0 40 Q600 -20 1200 40 L1200 61 Z" fill="#111"/></svg>
  <div class="footer-brand">harbourline</div>
  <div class="footer-col col-quick">
    <h4>Quick Links</h4>
    <ul><li>Our Company</li><li>Our Team</li><li>Harbourline IT Partners</li><li>Contact Us</li></ul>
  </div>
  <div class="footer-col col-useful">
    <h4>Useful links</h4>
    <ul><li>Services</li><li>Blog</li><li>Videos</li><li>Team Portal</li></ul>
  </div>
  <div class="footer-rule"></div>
  <p class="copyright">Copyright 2025 All Rights Reserved</p>
</footer>

</body>
</html>
```